A-Stand Directional Sign Design

Objective:
We need a professional graphic design for an A-Stand sign that will guide customers arriving in our parking lot to our office. The design should be visually clear, welcoming, and aligned with our brand identity.
REQUIREMENTS:
Two versions of the design:
- One with an arrow pointing left
- One with an arrow pointing right
(This allows us to place the A-Stand anywhere and flip the graphic as needed.)
DIMENSIONS:
- Viewable Area: 30" x 40"
BRAND ALIGNMENT:
- Colors, fonts, and overall style should match our website: www.glidemarrow.com
- Clean, modern, and professional look consistent with our aviation/tourism brand
CONTENT:
- Clear directional arrow (left or right depending on version)
- Text: “Office Entrance” or similar concise wording (designers may propose alternatives if they improve clarity)
READABILITY:
- Bold, high-contrast design for visibility from a distance
- Simple layout that avoids clutter
DELIVERABLES:
- Final artwork in print-ready format (PDF preferred)
- Two versions: Arrow Left and Arrow Right
DESIGN GOAL:
Ensure customers can easily find our office upon arrival, while reinforcing glideMARROW’s professional and welcoming brand image.
Target Market(s)
Tourism
Look and feel

```html
<!DOCTYPE html>
<html lang="en">
<head>
<meta charset="utf-8">
<title>glideMARROW – Office Entrance A-Stand Signs</title>
<link rel="stylesheet" href="https://fonts.googleapis.com/css2?family=Montserrat:wght@600;800&display=swap">
<style>
  :root {
    --page-bg: #f4f5f7;
    --panel-white: #ffffff;
    --panel-edge: #d9dce1;
    --brand-blue: #0a62e8;
    --logo-blue: #2f63b4;
    --photo-light: #8fb0e6;
    --photo-mid: #5b82c9;
    --photo-deep: #34589f;
    --headline: #ffffff;
  }
  * { box-sizing: border-box; margin: 0; padding: 0; }
  html, body {
    width: 1200px;
    height: 801px;
    overflow: hidden;
    background: var(--page-bg);
  }
  .sign-set {
    width: 1200px;
    height: 801px;
    display: flex;
    justify-content: center;
    align-items: center;
    gap: 90px;
  }
  .sign-panel {
    width: 500px;
    height: 667px;
    background: var(--panel-white);
    border: 1px solid var(--panel-edge);
    display: flex;
    flex-direction: column;
    overflow: hidden;
  }
  .sign-header {
    height: 300px;
    display: flex;
    flex-direction: column;
    align-items: center;
    padding-top: 48px;
  }
  .brand-mark {
    display: flex;
    align-items: center;
    gap: 10px;
  }
  .brand-dot {
    width: 22px;
    height: 22px;
    border-radius: 50%;
    background: var(--logo-blue);
  }
  .brand-name {
    font-family: "Montserrat", sans-serif;
    font-weight: 600;
    font-size: 26px;
    color: var(--logo-blue);
    letter-spacing: 0.5px;
  }
  .direction-arrow {
    margin-top: 46px;
    width: 320px;
    height: 140px;
  }
  .direction-arrow path {
    fill: var(--brand-blue);
    stroke: var(--brand-blue);
    stroke-width: 18;
    stroke-linejoin: round;
  }
  .arrow-left { transform: scaleX(-1); }
  .sign-feature {
    position: relative;
    flex: 1;
    display: flex;
    align-items: center;
    justify-content: center;
  }
  .feature-photo {
    position: absolute;
    inset: 0;
    background: linear-gradient(180deg, var(--photo-light) 0%, var(--photo-mid) 55%, var(--photo-deep) 100%);
  }
  .feature-headline {
    position: relative;
    font-family: "Montserrat", sans-serif;
    font-weight: 800;
    color: var(--headline);
    text-align: center;
    line-height: 1.02;
    text-transform: uppercase;
  }
  .feature-headline .line-one { display: block; font-size: 64px; }
  .feature-headline .line-two { display: block; font-size: 66px; }
</style>
</head>
<body>
  <main class="sign-set">
    <section class="sign-panel sign-right">
      <header class="sign-header">
        <div class="brand-mark">
          <span class="brand-dot"></span>
          <span class="brand-name">glideMARROW</span>
        </div>
        <svg class="direction-arrow" viewBox="0 0 320 140" aria-label="Arrow pointing right">
          <path d="M14 48 H200 V14 L306 70 L200 126 V92 H14 Z"/>
        </svg>
      </header>
      <div class="sign-feature">
        <div class="feature-photo" role="img" aria-label="Blue-toned photo of a helicopter parked on a wet helipad under a cloudy sky"></div>
        <h1 class="feature-headline"><span class="line-one">Office</span><span class="line-two">Entrance</span></h1>
      </div>
    </section>

    <section class="sign-panel sign-left">
      <header class="sign-header">
        <div class="brand-mark">
          <span class="brand-dot"></span>
          <span class="brand-name">glideMARROW</span>
        </div>
        <svg class="direction-arrow arrow-left" viewBox="0 0 320 140" aria-label="Arrow pointing left">
          <path d="M14 48 H200 V14 L306 70 L200 126 V92 H14 Z"/>
        </svg>
      </header>
      <div class="sign-feature">
        <div class="feature-photo" role="img" aria-label="Blue-toned photo of a helicopter parked on a wet helipad under a cloudy sky"></div>
        <h1 class="feature-headline"><span class="line-one">Office</span><span class="line-two">Entrance</span></h1>
      </div>
    </section>
  </main>
</body>
</html>
```